Web Design Project

Brightfold Publishing owns and operates a large number of editorial websites. These websites provides mostly consumers in the financial services space with information and price comparisons for a particular service.

Brightfold Publishing, as the holding company for each of these sites, currently has no website. We need to build a website targeted towards potential partners for our websites. The idea being that when we start a conversation with a partner, they can view our site and obtain some basic information about who we are.

The structure of the site is to be very simple, containing only a brief description about who we are, our contact details and a list of some of our websites:
• CoverVault.net.au
• MotorPolicyCheck.com.au
• DwellingCoverCheck.com.au
• MedicalCoverCheck.com.au
• LegacyCoverCheck.com.au
• JourneyCoverCheck.com.au
• AnimalCoverCheck.com.au
• PrivateLendingCheck.com.au
• MobileCoolingUnit.com.au
• FixedSavingsYield.com.au
• ThriftyHousehold.com.au
• CoinNana.com.au
• TameYourPlastic.com.au
• PurseMinder.com.au
• ThirdPartyClaimsCoverNational.com.au
• Trade-Cover.com.au
• MotorPolicyProviders.com.au
• MedicalCoverProviders.com.au
• DwellingCoverHub.com
• LegacyCoverHub.com
• EarningsShieldCoverHub.com
• MedicalCoverHub.com
• AnimalCoverHub.com
• PrivateLendingHub.com
• ChargePlasticHub.com
• DwellingLendingHub.com
• RetireNestEgg.net.au

The design of the site should say 'Internet company', 'professional', 'fresh thinking'. The design should not look like a corporate site that you would see from any corporate services business with images of people in suits. We are ultimately an Internet business and there should be a unique feel to the site.

We are open to a suggestion of a colour pallet as the holding company does not have an established logo.

Some sites that we like are:

http://www.quillmarsh-studio.co.uk/#home
http://previewbox00.layoutdock.example/wt_52418/index.html
http://previewbox00.layoutdock.example/wordpress_61942/
http://ponderloop.example/
http://www.brindlux.example/
http://www.tobiasvrankel.example/
http://www.slickfrontdoors.example/Corporate/design-ideas-detail.html?id=4197
http://pairmint.example/
http://orvendal.example/

Reason: Hi all, Apologies, but I need to extend the timeline. One of our key stakeholders is away for the next week. There are a few good designs that we have received to date and there are some tweaks that we would like to see before making a final decision. Thank you to everyone that has submitted designs - Have a great new year. Derek

Reason: Sorry to have to delay the deadline on this, but we did not find anything in the designs really resonated with us. We will have a further think about the existing designs that have been submitted and how we can provide more specific feedback to the designers to make some modifications to the designs.

Target Market(s)

We are targeting insurance companies / brokers that we are talking to. The idea is that we show a professional face to them.

Industry/Entity Type

Financial

Requirements
Must have
• Home Page (possibly integrated with About us details)
Contact Us
Our Sites

```html
<!DOCTYPE html>
<html lang="en">
<head>
<meta charset="utf-8">
<title>Brightfold Publishing</title>
<link href="https://fonts.googleapis.com/css2?family=Ubuntu:wght@400;500;700&family=Arimo:wght@400;700&display=swap" rel="stylesheet">
<style>
:root{
  --dark:#2b2a28;
  --dark-2:#3a3936;
  --orange:#f08a00;
  --orange-light:#ffb400;
  --text:#2e2e2e;
  --muted:#555;
  --white:#fff;
  --field:#3b3b3b;
  --rule:#bdbdbd;
}
*{margin:0;padding:0;box-sizing:border-box}
html,body{width:1085px;height:1200px;overflow:hidden}
body{position:relative;background:#fff;font-family:Arimo,Arial,sans-serif;color:var(--text)}
.abs{position:absolute}
.header-band{left:0;top:0;width:1085px;height:490px;background:linear-gradient(180deg,#1f1e1c 0%,#34332f 45%,#262522 100%)}
.page-fade{left:0;top:860px;width:1085px;height:272px;background:linear-gradient(180deg,#fff 0%,#e6e6e6 100%)}
.logo-box{left:123px;top:64px;width:302px;height:72px;border:2px solid #5a5955;border-radius:12px;background:#2a2927;display:flex;align-items:center;justify-content:center;gap:10px}
.logo-box .mark{width:14px;height:14px;background:var(--orange)}
.logo-box span{font-family:Ubuntu,sans-serif;font-weight:700;font-size:23px;color:var(--white);letter-spacing:.5px}
.nav{left:507px;top:45px;display:flex;height:34px}
.nav a{font-family:Ubuntu,sans-serif;font-size:15px;color:#eee;text-decoration:none;display:flex;align-items:center;justify-content:center;height:34px;border-right:1px solid #444}
.nav a:last-child{border-right:none}
.nav .home{width:94px;background:linear-gradient(#f5a200,#d97f00);border:1px solid #f7b84a;color:#fff}
.nav .about{width:132px}.nav .projects{width:122px}.nav .contact{width:128px}
.header-phone{left:760px;top:128px;display:flex;align-items:center;gap:10px;font-family:Ubuntu,sans-serif;font-size:28px;color:#eee;letter-spacing:1px}
.header-phone svg{width:26px;height:26px}
.slider-frame{left:108px;top:178px;width:885px;height:360px;background:#fff}
.slider{left:118px;top:188px;width:864px;height:350px;background:radial-gradient(ellipse at 62% 40%,#ffc21a 0%,#f7a000 45%,#e88300 100%);overflow:hidden}
.slider h2{position:absolute;left:67px;top:18px;font-family:Ubuntu,sans-serif;font-weight:500;font-size:28px;color:#fff}
.shot{position:absolute;left:58px;top:66px;width:300px;height:262px;background:linear-gradient(160deg,#fdfdfd,#dcdcdc);border:6px solid #f3f3f3;transform:perspective(600px) rotateY(8deg) rotateZ(-1.5deg);box-shadow:0 6px 14px rgba(0,0,0,.25)}
.slide-title{position:absolute;right:60px;top:56px;font-family:Ubuntu,sans-serif;font-weight:700;font-size:38px;color:#111;text-align:right;line-height:1}
.slide-title em{font-style:normal;color:#fff}
.slide-url{position:absolute;right:60px;top:108px;font-family:Ubuntu,sans-serif;font-weight:700;font-size:18px;color:#222;letter-spacing:.5px}
.slide-copy{position:absolute;left:380px;top:165px;width:454px;font-size:12px;line-height:19.2px;color:#fff;text-align:justify}
.view-btn{position:absolute;left:682px;top:262px;width:128px;height:46px;border-radius:14px;background:linear-gradient(#fff 0%,#f2f2f2 50%,#cfcfcf 100%);font-family:Ubuntu,sans-serif;font-weight:700;font-size:16px;color:#333;display:flex;align-items:center;justify-content:center;box-shadow:0 2px 4px rgba(0,0,0,.3)}
.arrow{position:absolute;top:160px;font-size:40px;color:#ffe2a8;font-family:Ubuntu,sans-serif}
.slider-shadow{left:145px;top:546px;width:810px;height:24px;border-radius:50%;background:radial-gradient(ellipse at center,rgba(0,0,0,.45) 0%,rgba(0,0,0,0) 70%)}
.section-title{font-family:Ubuntu,sans-serif;font-weight:500;color:#222}
.section-title em{font-style:normal;color:var(--orange)}
.welcome-title{left:130px;top:598px;font-size:28px;display:flex;align-items:center;gap:10px}
.welcome-title .mark{width:14px;height:14px;background:var(--orange)}
.rule{height:0;border-top:1px dotted var(--rule)}
.welcome-rule{left:115px;top:648px;width:578px}
.intro{left:118px;top:660px;width:575px;font-size:12px;line-height:21px;text-align:justify}
.intro-2{left:118px;top:765px;width:575px;font-size:12px}
.contact-line{left:116px;top:800px;display:flex;align-items:baseline;gap:14px}
.contact-line .big-phone{font-family:Ubuntu,sans-serif;font-size:32px;color:var(--orange)}
.contact-line .or{font-size:12px}
.contact-line .mail{font-family:Ubuntu,sans-serif;font-size:16px;color:var(--orange);letter-spacing:.5px}
.query-title{left:114px;top:864px;font-size:24px}
.query-rule{left:114px;top:900px;width:578px}
.field{background:var(--field);border:2px solid #555;border-radius:12px;color:#eee;font-size:12px;padding-left:14px;display:flex;align-items:center;box-shadow:inset 0 2px 4px rgba(0,0,0,.5),0 1px 0 #fff}
.f-name{left:108px;top:922px;width:248px;height:36px}
.f-phone{left:108px;top:980px;width:248px;height:36px}
.f-email{left:108px;top:1036px;width:248px;height:36px}
.f-details{left:394px;top:920px;width:286px;height:114px;align-items:flex-start;padding-top:10px}
.submit{left:583px;top:1046px;width:87px;height:35px;border-radius:12px;background:linear-gradient(#5a5a5a,#2e2e2e);color:#fff;font-family:Ubuntu,sans-serif;font-weight:700;font-size:14px;display:flex;align-items:center;justify-content:center;box-shadow:0 2px 4px rgba(0,0,0,.35)}
.partners{left:720px;top:617px;width:244px;height:472px;border:1px solid #d6d6d6;border-radius:14px;background:linear-gradient(#fff,#f0f0f0);box-shadow:0 1px 3px rgba(0,0,0,.15)}
.partners header{height:42px;border-bottom:1px solid #ddd;border-radius:14px 14px 0 0;background:linear-gradient(#fff,#ececec);display:flex;align-items:center;justify-content:space-between;padding:0 8px 0 19px}
.partners header h3{font-family:Ubuntu,sans-serif;font-weight:500;font-size:23px;color:#222}
.partners header h3 em{font-style:normal;color:var(--orange)}
.partners header .ctrl{display:flex;gap:3px}
.partners ul{list-style:none;padding:12px 0 0 32px}
.partners li{font-family:Ubuntu,sans-serif;font-size:11px;color:#333;height:28.8px;line-height:28.8px;position:relative;letter-spacing:.2px}
.partners li::before{content:"";position:absolute;left:-14px;top:10px;border-left:4px solid #444;border-top:4px solid transparent;border-bottom:4px solid transparent}
.footer{left:0;top:1132px;width:1085px;height:68px;background:var(--dark-2)}
.footer .brand{position:absolute;left:144px;top:22px;width:22px;height:22px;border-radius:50%;background:#555}
.footer nav{position:absolute;left:309px;top:14px;font-size:12px;color:#eee;letter-spacing:.3px;word-spacing:2px}
.footer nav span{margin:0 13px;color:#bbb}
.footer .copy{position:absolute;left:352px;top:37px;font-size:12px;color:#eee}
.footer address{position:absolute;right:128px;top:6px;text-align:right;font-style:normal;font-family:Ubuntu,sans-serif;font-size:11px;line-height:19.5px;color:#fff}
.footer address strong{font-size:12.5px}
</style>
</head>
<body>
<div class="abs header-band"></div>
<div class="abs page-fade"></div>

<div class="abs logo-box"><i class="mark"></i><span>BRIGHTFOLD PUBLISHING</span></div>

<nav class="abs nav">
  <a class="home" href="#">Home</a>
  <a class="about" href="#">About US</a>
  <a class="projects" href="#">Projects</a>
  <a class="contact" href="#">Contact Us</a>
</nav>

<div class="abs header-phone">
  <svg viewBox="0 0 26 26"><rect x="1" y="1" width="24" height="24" rx="4" fill="#111" stroke="#555"/><path d="M9 7h4v3h-2v6h2v3H9z" fill="#eee"/></svg>
  <span>02 9417 6620</span>
</div>

<div class="abs slider-frame"></div>
<section class="abs slider">
  <h2>We get you leads</h2>
  <div class="shot" role="img" aria-label="Screenshot of the Thrifty Household website homepage"></div>
  <div class="slide-title">THRIFTY <em>HOUSEHOLD</em></div>
  <div class="slide-url">www.thriftyhousehold.com.au</div>
  <p class="slide-copy">Bills, debt, petrol, expenses, insurance, more bills, credit cards, groceries, even more bills. And bills. Lots of bills. Life can often feel like a tireless parade of ways to drain your bank account. None of us are strangers to the miserable feeling of watching fresh wages fritter away in a thousand directions before you've even had a chance to enjoy them.</p>
  <div class="view-btn">View Details</div>
  <span class="arrow" style="left:6px">&#10216;</span>
  <span class="arrow" style="right:6px">&#10217;</span>
</section>
<div class="abs slider-shadow"></div>

<h1 class="abs section-title welcome-title"><i class="mark"></i><span>Welcome <em>Message</em></span></h1>
<div class="abs rule welcome-rule"></div>
<p class="abs intro">Brightfold Publishing is an Australian-based internet marketingcompany.&nbsp; We specialise in attractingcustomers from our directory of more than 100 sites to our network of trustedpartners.&nbsp; Our skill lies in generating targetedtraffic to our range of websites and identifying the right partners for each ofthe sites, ensuring that the visitors to our sites get what they are lookingfor.</p>
<p class="abs intro-2">If you are interested in partnering with us on one ormultiple of our sites, please contact us at :</p>
<div class="abs contact-line">
  <span class="big-phone">02 9417 6620</span>
  <span class="or">Or Email us @</span>
  <span class="mail">info@brightfoldpublishing.com.au</span>
</div>

<h2 class="abs section-title query-title">For more Info, <em>Send us your Query</em></h2>
<div class="abs rule query-rule"></div>
<div class="abs field f-name">---- Name -----</div>
<div class="abs field f-phone">---- Phone -----</div>
<div class="abs field f-email">---- Email -----</div>
<div class="abs field f-details">---- Your requirement details -----</div>
<div class="abs submit">Submit</div>

<aside class="abs partners">
  <header>
    <h3>Our <em>Partners</em></h3>
    <div class="ctrl">
      <svg width="18" height="18" viewBox="0 0 18 18"><circle cx="9" cy="9" r="8" fill="#222"/><path d="M5 11l4-5 4 5z" fill="#fff"/></svg>
      <svg width="18" height="18" viewBox="0 0 18 18"><circle cx="9" cy="9" r="8" fill="#222"/><path d="M5 7l4 5 4-5z" fill="#fff"/></svg>
    </div>
  </header>
  <ul>
    <li>CoverVault.net.au</li>
    <li>MotorPolicyCheck.com.au</li>
    <li>DwellingCoverCheck.com.au</li>
    <li>MedicalCoverCheck.com.au</li>
    <li>LegacyCoverCheck.com.au</li>
    <li>JourneyCoverCheck.com.au</li>
    <li>AnimalCoverCheck.com.au</li>
    <li>PrivateLendingCheck.com.au</li>
    <li>MobileCoolingUnit.com.au</li>
    <li>FixedSavingsYield.com.au</li>
    <li>ThriftyHousehold.com.au</li>
    <li>CoinNana.com.au</li>
    <li>TameYourPlastic.com.au</li>
    <li>PurseMinder.com.au</li>
  </ul>
</aside>

<footer class="abs footer">
  <i class="brand"></i>
  <nav>Home<span>/</span>About Us<span>/</span>Projects<span>/</span>Contact Us</nav>
  <p class="copy">Copyright Brightfold Publishing &copy; 2011-12.</p>
  <address><strong>Brightfold Publishing Pty Ltd</strong><br>Suite 412, 18 Harrow Lane,<br>Marlow Heights NSW 2031</address>
</footer>
</body>
</html>
```